Yacht, Boats, Watersports company needs a redesign of business card

Hello Designers!
We are a Boat dealership company that sells fun in the water, we sell boats, Yachts, Kayaks and also yacht WaterSport toys. We are looking to redesign our business cards in to something a little bit more sophisticated. in a way that we can make better use of our company colors. I'm attaching a zipped file containing the company 3 sets of company logo which one is an horizontal another one is a vertical and also a chromed 3d logo. Also is included two set of business cards that we use and also some designs that i think it's interesting. We use PMS 2026c Orange and PMS 7687C Blue. I would like to see at least two different options with the orange as accent and also using blue as an accent color. It's really important for the business cards to have a font option and size that is legible to most people. Our current website is wwww.coralpennant.com. Please visit if you want to have a better feeling of the Boat dealership
You can send Single sided or double side options. We are now using single sided but we may be open for a double side option if we really like the design.
Target Market(s)
Marine, boat sales, yacht sales, water toys sales/
Contact Information for Business Card
Name: Dale Whitcombe
Address: 212 North Fenwick Lane,
Harbor Point, FL 33019
Phone: 954-731-8842
Fax: 954:731-8843
Cell: 954-382-1490
Email: dw@coralpennant.com
Website: coralpennant.com
Requirements
Must have
- the current information of the business card provided.
logo
use the PMS Colors
Nice to have
- a touch of elegance and sophistication but simple
Should not have
- should not have any typography that is hard to read, the card should be simple but yet sophisticated.

```html
<!DOCTYPE html>
<html lang="en">
<head>
<meta charset="utf-8">
<title>Coral Pennant – Business Card</title>
<link href="https://fonts.googleapis.com/css2?family=Poppins:wght@400;500;600&display=swap" rel="stylesheet">
<style>
  :root {
    --brand-blue: #1f6db5;
    --brand-orange: #ef8a25;
    --mark-gold: #ffd84a;
    --text-grey: #4a4a4a;
    --rule-grey: #8a8a8a;
    --paper: #ffffff;
    --backdrop: #e9e9e9;
  }
  * { margin: 0; padding: 0; box-sizing: border-box; }
  html, body { width: 1125px; height: 1200px; overflow: hidden; }
  body { background: var(--backdrop); font-family: 'Poppins', sans-serif; position: relative; }

  .card { position: absolute; left: 150px; width: 826px; height: 471px; overflow: hidden; }
  .card--front { top: 106px; background: var(--paper); }
  .card--back { top: 639px; background: var(--brand-orange); }

  .brand { position: absolute; display: flex; flex-direction: column; align-items: center; }
  .brand__dot { border-radius: 50%; }
  .brand__name { font-weight: 600; letter-spacing: 1px; white-space: nowrap; }

  .card--front .brand { left: 450px; top: 48px; width: 330px; }
  .card--front .brand__dot { width: 80px; height: 80px; border: 7px solid var(--brand-blue); }
  .card--front .brand__name { color: var(--brand-blue); font-size: 27px; margin-top: 24px; }

  .card--back .brand { left: 0; right: 0; top: 114px; }
  .card--back .brand__dot { width: 124px; height: 124px; border: 10px solid var(--mark-gold); }
  .card--back .brand__name { color: var(--mark-gold); font-size: 34px; margin-top: 22px; }

  .holder { position: absolute; left: 41px; top: 256px; color: var(--brand-blue); font-size: 25px; font-weight: 600; letter-spacing: 0.3px; }
  .rule { position: absolute; left: 41px; top: 305px; width: 735px; height: 1px; background: var(--rule-grey); }

  .contacts { position: absolute; left: 41px; top: 322px; list-style: none; }
  .contacts li { display: flex; align-items: center; height: 23.5px; font-size: 18px; color: var(--text-grey); }
  .contacts svg { width: 16px; height: 16px; margin-right: 11px; fill: var(--brand-blue); flex: none; }

  .address { position: absolute; right: 51px; top: 370px; text-align: right; font-size: 18px; line-height: 24px; color: var(--text-grey); }

  .footer-band { position: absolute; left: 0; bottom: 0; width: 826px; height: 40px; }
  .web { position: absolute; right: 33px; bottom: 7px; color: var(--paper); font-size: 18.5px; }
</style>
</head>
<body>

<section class="card card--front" aria-label="Business card front">
  <div class="brand">
    <div class="brand__dot"></div>
    <div class="brand__name">CORAL PENNANT</div>
  </div>

  <h1 class="holder">DALE WHITCOMBE</h1>
  <div class="rule"></div>

  <ul class="contacts">
    <li><svg viewBox="0 0 24 24"><path d="M6.6 10.8a15.1 15.1 0 0 0 6.6 6.6l2.2-2.2c.3-.3.7-.4 1-.2 1.1.4 2.3.6 3.6.6.6 0 1 .4 1 1V20c0 .6-.4 1-1 1A17 17 0 0 1 3 4c0-.6.4-1 1-1h3.5c.6 0 1 .4 1 1 0 1.3.2 2.5.6 3.6.1.3 0 .7-.2 1z"/></svg>954-731-8842</li>
    <li><svg viewBox="0 0 24 24"><path d="M7 1h10a2 2 0 0 1 2 2v18a2 2 0 0 1-2 2H7a2 2 0 0 1-2-2V3a2 2 0 0 1 2-2zm0 3v14h10V4zm5 15.5a1 1 0 1 0 0 2 1 1 0 0 0 0-2z"/></svg>954-382-1490</li>
    <li><svg viewBox="0 0 24 24"><path d="M6 2h9l3 3v5H6zM3 11h18a1 1 0 0 1 1 1v8a1 1 0 0 1-1 1H3a1 1 0 0 1-1-1v-8a1 1 0 0 1 1-1zm3 3v2h12v-2z"/></svg>954-731-8843</li>
    <li><svg viewBox="0 0 24 24"><path d="M2 5h20v14H2zm2 2v.5l8 5 8-5V7l-8 5z"/></svg>dw@coralpennant.com</li>
  </ul>

  <p class="address">212 North Fenwick Lane<br>Harbor Point, FL 33019</p>

  <svg class="footer-band" viewBox="0 0 826 40" preserveAspectRatio="none" aria-hidden="true">
    <rect x="0" y="20" width="470" height="5" fill="var(--brand-orange)"/>
    <path d="M0 27 H480 V40 H0 Z" fill="var(--brand-blue)"/>
    <path d="M466 40 C486 40 482 4 512 4 H826 V40 Z" fill="var(--brand-blue)"/>
  </svg>
  <span class="web">www.coralpennant.com</span>
</section>

<section class="card card--back" aria-label="Business card back">
  <div class="brand">
    <div class="brand__dot"></div>
    <div class="brand__name">CORAL PENNANT</div>
  </div>
</section>

</body>
</html>
```